Info graphics

We have four infographics that we want recreated. We want the same information displayed but original artwork

Requirements
Must have
• We require a re-creation of each of the 4 infographics attached.

```html
<!DOCTYPE html>
<html lang="en">
<head>
<meta charset="utf-8">
<title>Comparing 4G and 5G</title>
<link rel="stylesheet" href="https://fonts.googleapis.com/css2?family=Ubuntu:wght@500;700&display=swap">
<style>
  :root {
    --blue: #29abe2;
    --orange: #e8a631;
    --dark: #2b2b2b;
    --ink: #000000;
    --white: #ffffff;
    --paper: #ffffff;
    --grey: #6b6f73;
  }
  * { box-sizing: border-box; margin: 0; padding: 0; }
  html, body { width: 1200px; height: 500px; overflow: hidden; background: var(--paper); }
  .canvas {
    position: relative; width: 1200px; height: 500px; overflow: hidden;
    font-family: "Ubuntu", sans-serif; color: var(--white);
  }
  .artwork { position: absolute; inset: 0; }
  .title {
    position: absolute; left: 435px; top: 29px; width: 330px; height: 66px;
    background: var(--dark); border-radius: 8px;
    display: flex; align-items: center; justify-content: center;
    font-size: 23px; font-weight: 500; letter-spacing: 0.5px;
  }
  .stat {
    position: absolute; border-radius: 4px;
    font-size: 18px; font-weight: 500; line-height: 20px; letter-spacing: 0.4px;
    display: flex; flex-direction: column; justify-content: center;
    padding: 0 17px;
  }
  .stat--4g { background: var(--blue); text-align: right; }
  .stat--5g { background: var(--orange); text-align: left; }
  .stat sup { font-size: 10px; line-height: 0; }
  .gen-badge {
    position: absolute; top: 297px; width: 48px; height: 48px; border-radius: 3px;
    display: flex; align-items: center; justify-content: center;
    font-size: 20px; font-weight: 500;
  }
  .gen-badge--4g { left: 527px; background: var(--blue); }
  .gen-badge--5g { left: 631px; background: var(--orange); }
</style>
</head>
<body>
<div class="canvas">
  <svg class="artwork" width="1200" height="500" viewBox="0 0 1200 500">
    <defs>
      <g id="icon-hourglass" fill="none" stroke="#fff" stroke-width="1.8">
        <path d="M-6 -9 H6 M-6 9 H6 M-5 -9 C-5 -2 5 -2 5 0 C5 2 -5 2 -5 9 M5 -9 C5 -2 -5 -2 -5 0 C-5 2 5 2 5 9"/>
      </g>
      <g id="icon-traffic" fill="none" stroke="#fff" stroke-width="1.5">
        <rect x="-5" y="-10" width="11" height="20" rx="2"/>
        <path d="M-1 -3 L1 -6 L3 -3 M1 -6 V3 M-8 2 L-6 6 L-4 2 M-6 6 V-2"/>
      </g>
      <g id="icon-arrow" fill="#fff">
        <path d="M0 -11 L7 -2 H3 V10 H-3 V-2 H-7 Z"/>
      </g>
      <g id="icon-bars" fill="#fff">
        <rect x="-10" y="-3" width="3.5" height="12"/>
        <rect x="-4.5" y="-8" width="3.5" height="17"/>
        <rect x="1" y="1" width="3.5" height="8"/>
        <rect x="6.5" y="-5" width="3.5" height="14"/>
        <rect x="-11" y="9" width="22" height="1.5"/>
      </g>
      <g id="icon-density" fill="none" stroke="#fff" stroke-width="1.3">
        <circle r="10"/>
        <circle cx="0" cy="-5" r="2.2"/><circle cx="-5" cy="-1" r="2.2"/>
        <circle cx="5" cy="-1" r="2.2"/><circle cx="0" cy="3" r="2.2"/>
        <circle cx="-4" cy="6" r="2"/><circle cx="4" cy="6" r="2"/>
      </g>
    </defs>

    <!-- corner bands -->
    <polygon points="0,0 275,0 0,203" fill="var(--blue)"/>
    <polygon points="927,0 1200,0 1200,203" fill="var(--blue)"/>
    <polygon points="0,347 205,500 0,500" fill="var(--orange)"/>
    <polygon points="1200,342 985,500 1200,500" fill="var(--orange)"/>

    <!-- corner motifs -->
    <rect x="24" y="26" width="78" height="88" rx="10" fill="#e0a23a" opacity="0.85" role="img" aria-label="Illustration of a communications satellite"/>
    <g class="mobile-phone">
      <rect x="1114" y="27" width="36" height="70" rx="6" fill="var(--grey)"/>
      <rect x="1119" y="34" width="26" height="22" rx="3" fill="#8fd6f2"/>
      <g fill="#d5d8da">
        <rect x="1119" y="62" width="7" height="4"/><rect x="1128" y="62" width="7" height="4"/><rect x="1137" y="62" width="7" height="4"/>
        <rect x="1119" y="70" width="7" height="4"/><rect x="1128" y="70" width="7" height="4"/><rect x="1137" y="70" width="7" height="4"/>
        <rect x="1119" y="78" width="7" height="4"/><rect x="1128" y="78" width="7" height="4"/><rect x="1137" y="78" width="7" height="4"/>
      </g>
    </g>
    <g class="wifi" fill="none" stroke="var(--blue)" stroke-width="6" stroke-linecap="round">
      <path d="M24 446 A46 46 0 0 1 88 446"/>
      <path d="M34 457 A31 31 0 0 1 78 457"/>
      <path d="M44 467 A17 17 0 0 1 68 467"/>
      <circle cx="56" cy="477" r="5" fill="var(--blue)" stroke="none"/>
    </g>
    <path class="handset" d="M1160 408 L1172 418 C1182 440 1168 468 1138 482 L1110 480 L1100 468 L1114 458 L1126 466 C1144 456 1154 442 1152 426 L1146 416 Z" fill="#1e8fc4"/>

    <!-- connectors -->
    <g stroke-width="3">
      <line x1="425" y1="148" x2="558" y2="148" stroke="var(--blue)"/>
      <line x1="403" y1="199" x2="490" y2="199" stroke="var(--blue)"/>
      <line x1="389" y1="269" x2="470" y2="269" stroke="var(--blue)"/>
      <line x1="403" y1="349" x2="495" y2="349" stroke="var(--blue)"/>
      <line x1="425" y1="397" x2="558" y2="397" stroke="var(--blue)"/>
      <line x1="642" y1="148" x2="774" y2="148" stroke="var(--orange)"/>
      <line x1="709" y1="199" x2="797" y2="199" stroke="var(--orange)"/>
      <line x1="730" y1="269" x2="811" y2="269" stroke="var(--orange)"/>
      <line x1="705" y1="349" x2="797" y2="349" stroke="var(--orange)"/>
      <line x1="642" y1="397" x2="774" y2="397" stroke="var(--orange)"/>
    </g>

    <!-- ring -->
    <circle cx="600" cy="269" r="131" fill="none" stroke="var(--dark)" stroke-width="21"/>

    <!-- tower scene -->
    <rect x="528" y="188" width="144" height="90" rx="6" fill="#eef3f6" role="img" aria-label="Illustration of a signal tower with two people holding devices"/>
    <line x1="485" y1="280" x2="718" y2="280" stroke="var(--ink)" stroke-width="3"/>

    <!-- 4G to 5G arrow -->
    <path d="M589 319 H606 V313 L617 321 L606 329 V323 H589 Z" fill="var(--dark)"/>

    <!-- icon nodes -->
    <g fill="var(--blue)">
      <circle cx="558" cy="148" r="19"/><circle cx="490" cy="199" r="19"/>
      <circle cx="470" cy="269" r="19"/><circle cx="495" cy="349" r="19"/>
      <circle cx="558" cy="397" r="19"/>
    </g>
    <g fill="var(--orange)">
      <circle cx="642" cy="148" r="19"/><circle cx="709" cy="199" r="19"/>
      <circle cx="730" cy="269" r="19"/><circle cx="705" cy="349" r="19"/>
      <circle cx="642" cy="397" r="19"/>
    </g>
    <use href="#icon-hourglass" x="558" y="148"/><use href="#icon-hourglass" x="642" y="148"/>
    <use href="#icon-traffic" x="490" y="199"/><use href="#icon-traffic" x="709" y="199"/>
    <use href="#icon-arrow" x="470" y="269"/><use href="#icon-arrow" x="730" y="269"/>
    <use href="#icon-bars" x="495" y="349"/><use href="#icon-bars" x="705" y="349"/>
    <use href="#icon-density" x="558" y="397"/><use href="#icon-density" x="642" y="397"/>
  </svg>

  <h1 class="title">Comparing 4G&nbsp; and 5G</h1>

  <div class="gen-badge gen-badge--4g">4G</div>
  <div class="gen-badge gen-badge--5g">5G</div>

  <div class="stat stat--4g" style="left:256px;top:130px;width:169px;height:37px;">Latency&nbsp; &lt; 1 ms</div>
  <div class="stat stat--4g" style="left:130px;top:181px;width:273px;height:57px;">Data Traffic<span>50 Exabytes/Month (2021</span></div>
  <div class="stat stat--4g" style="left:203px;top:248px;width:186px;height:57px;">Peak Data Rates<span>20 Gb/s</span></div>
  <div class="stat stat--4g" style="left:187px;top:317px;width:216px;height:57px;">Available Spectrum<span>30 GHz</span></div>
  <div class="stat stat--4g" style="left:151px;top:383px;width:274px;height:57px;">Connection Density<span>1 Million Connections/Km</span></div>

  <div class="stat stat--5g" style="left:774px;top:130px;width:170px;height:37px;">Latency&nbsp; &lt; 1 ms</div>
  <div class="stat stat--5g" style="left:797px;top:181px;width:272px;height:57px;">Data Traffic<span>50 Exabytes/Month (2021</span></div>
  <div class="stat stat--5g" style="left:811px;top:248px;width:186px;height:57px;">Peak Data Rates<span>20 Gb/s</span></div>
  <div class="stat stat--5g" style="left:797px;top:317px;width:216px;height:57px;">Available Spectrum<span>30 GHz</span></div>
  <div class="stat stat--5g" style="left:774px;top:383px;width:274px;height:57px;">Connection Density<span>1 Million Connections/Km<sup>2</sup></span></div>
</div>
</body>
</html>
```